Company Website Re-design for Software development consultancy

We would like our company website to be redesigned using our existing marketing collateral and website content as a guide

current site : www.brightkestrel.com.au

For the different pages types and content please base on the following site : https://www.quorvalabs.net/

We want a coded site - but will replace the content ourselves within the sections you provide to customise to our needs.

Target Market(s)

Medium to Large corporates needing software design and development services

Industry/Entity Type

Information Technology

Coding

Coded - Design and coding required

Number of Pages Required

5+ page

Font styles to use
Sans Serif

Colors
ec1f27
ffffff
000000

Requirements
Must have
• Align to colour scheme of existing collateral
• Include pages for the key areas of our busines - see : https://www.quorvalabs.net/
Nice to have
• image rotators - make the site interesting to the business visitor

```html
<!DOCTYPE html>
<html lang="en">
<head>
<meta charset="utf-8">
<title>Bright Kestrel — Software Development Consultancy</title>
<link href="https://fonts.googleapis.com/css2?family=Montserrat:wght@400;500;600;700&family=Open+Sans:wght@400;600&display=swap" rel="stylesheet">
<style>
:root{
  --red:#ec1f27;
  --white:#ffffff;
  --black:#000000;
  --ink:#222222;
  --text:#555555;
  --muted:#888888;
  --grey-band:#ececec;
  --footer:#1f1f1f;
  --line:#dddddd;
}
*{box-sizing:border-box;margin:0;padding:0}
html,body{width:1200px;height:3571px;overflow:hidden}
body{font-family:"Open Sans",Arial,sans-serif;color:var(--text);background:var(--white);position:relative}
.abs{position:absolute}
h1,h2,h3,h4,.nav a,.brand{font-family:"Montserrat",Arial,sans-serif}

/* header */
.site-header{position:absolute;left:0;top:0;width:1200px;height:100px;background:var(--white);border-top:4px solid var(--red)}
.brand{position:absolute;left:86px;top:30px;display:flex;align-items:center;gap:12px;font-weight:700;font-size:25px;color:var(--ink);letter-spacing:.5px}
.brand .mark{width:40px;height:40px;background:var(--red);border-radius:4px}
.nav{position:absolute;right:86px;top:44px;display:flex;gap:42px}
.nav a{font-size:13px;font-weight:500;color:var(--ink);text-decoration:none;letter-spacing:.3px}
.nav a.active{color:var(--red)}

/* hero */
.hero{position:absolute;left:0;top:100px;width:1200px;height:630px;background:linear-gradient(120deg,#3b3f44 0%,#5a5d60 40%,#2e3135 100%)}
.hero-shade{position:absolute;inset:0;background:linear-gradient(90deg,rgba(0,0,0,.55),rgba(0,0,0,.15))}
.hero h1{position:absolute;left:112px;top:200px;color:var(--white);font-weight:600;font-size:46px;line-height:1.1;letter-spacing:1px}
.hero h1 span{display:block;font-size:29px;font-weight:500;margin-top:10px}
.hero p{position:absolute;left:112px;top:322px;width:470px;color:#eee;font-size:12px;line-height:25px}
.btn-outline{position:absolute;left:112px;top:425px;width:175px;height:46px;border:2px solid var(--white);color:var(--white);font-family:"Montserrat",sans-serif;font-weight:600;font-size:14px;display:flex;align-items:center;justify-content:center;letter-spacing:.5px}
.dots{position:absolute;left:577px;top:600px;display:flex;gap:8px}
.dots i{width:10px;height:10px;border:1px solid var(--white);display:block}
.dots i.on{background:var(--red);border-color:var(--red)}

/* section headings */
.sec-title{position:absolute;left:0;width:1200px;text-align:center;font-weight:500;font-size:30px;color:var(--ink);letter-spacing:.5px}
.sec-title em{font-style:normal;color:var(--red)}
.sec-text{position:absolute;text-align:center;font-size:12.5px;line-height:29px;color:var(--text)}

/* clients */
.clients{position:absolute;left:140px;top:1048px;width:920px;display:flex;justify-content:space-between}
.clients span{width:120px;height:50px;background:#d6d6d6;border-radius:6px;display:block}

/* services */
.services{position:absolute;left:0;top:1165px;width:1200px;height:440px;background:var(--grey-band)}
.service{position:absolute;top:170px;width:300px;text-align:center}
.service .icon{width:76px;height:76px;margin:0 auto 18px;background:#f5c9cb;border:3px solid var(--red);border-radius:10px}
.service h3{font-weight:500;font-size:19px;color:var(--ink);letter-spacing:.5px;margin-bottom:12px}
.service p{font-size:12px;line-height:26px;color:var(--text)}

/* who */
.who-photo{position:absolute;left:172px;top:1762px;width:450px;height:353px;background:linear-gradient(135deg,#c8d3dc,#7d8c98 60%,#4e5861)}
.who-card{position:absolute;left:490px;top:1890px;width:523px;height:342px;background:var(--white);border:1px solid var(--line);box-shadow:0 2px 10px rgba(0,0,0,.08);padding:52px 46px}
.who-card h3{color:var(--red);font-weight:500;font-size:19px;margin-bottom:22px}
.who-card p{font-size:12px;line-height:27px;color:var(--text);text-align:justify}

/* testimonial */
.testimonial{position:absolute;left:0;top:2300px;width:1200px;height:290px;background:var(--red)}
.testimonial .quote{position:absolute;left:175px;top:76px;width:560px;color:var(--white);font-size:12px;line-height:24px}
.testimonial .qmark{position:absolute;color:var(--white);font-family:Georgia,serif;font-size:34px;line-height:34px}
.testimonial h4{position:absolute;left:178px;top:200px;color:var(--white);font-size:14px;font-weight:600}
.testimonial .date{position:absolute;left:178px;top:222px;color:var(--white);font-size:12px}
.testimonial .avatar{position:absolute;left:772px;top:42px;width:196px;height:196px;border-radius:50%;border:5px solid var(--white);background:linear-gradient(160deg,#d9b79a,#8c6a52)}
.testimonial svg{position:absolute;top:115px}

/* team */
.team-card{position:absolute;top:2880px;width:292px;height:230px;border:1px solid var(--line);background:var(--white);text-align:center;padding-top:118px}
.team-card .portrait{position:absolute;left:54px;top:-84px;width:184px;height:184px;border-radius:50%;border:5px solid #e6e6e6;background:linear-gradient(160deg,#b7c6cf,#6f7b84)}
.team-card h4{color:var(--red);font-weight:600;font-size:15px}
.team-card .role{font-size:11.5px;color:var(--muted);letter-spacing:1px;margin:6px 0 12px}
.team-card p{font-size:12px;line-height:24px;color:var(--text);padding:0 60px}

/* footer */
.site-footer{position:absolute;left:0;top:3185px;width:1200px;height:386px;background:var(--footer);color:var(--white)}
.foot-brand{position:absolute;left:95px;top:70px;width:280px;text-align:center}
.foot-brand .mark{width:104px;height:104px;background:var(--red);border-radius:6px;margin:0 auto 30px}
.foot-brand .name{font-family:"Montserrat",sans-serif;font-weight:700;font-size:26px;color:var(--white);white-space:nowrap}
.foot-col{position:absolute;top:45px}
.foot-col h4{font-weight:500;font-size:19px;margin-bottom:28px}
.foot-col .item{font-size:14px;line-height:19px;margin-bottom:16px}
.foot-col .link{font-size:13.5px;margin-bottom:13px;font-family:"Montserrat",sans-serif}
.field{width:264px;height:38px;background:var(--white);color:var(--ink);font-size:12px;padding:11px 12px;font-family:"Montserrat",sans-serif}
.btn-red{margin-top:14px;width:126px;height:36px;background:var(--red);color:var(--white);font-family:"Montserrat",sans-serif;font-weight:600;font-size:14px;display:flex;align-items:center;justify-content:center}
.socials{display:flex;gap:8px;margin-top:22px}
.socials span{width:36px;height:36px;border:2px solid var(--white);border-radius:50%;display:block}
.foot-rule{position:absolute;left:120px;top:315px;width:960px;height:1px;background:#3a3a3a}
.copyright{position:absolute;left:0;top:344px;width:1200px;text-align:center;font-size:13px;color:#ddd}
</style>
</head>
<body>

<header class="site-header">
  <div class="brand"><span class="mark"></span>BRIGHT KESTREL</div>
  <nav class="nav">
    <a class="active">HOME</a><a>SOLUTIONS</a><a>SERVICES</a><a>INDUSTRIES</a><a>RESOURCES</a><a>CONTACT US</a>
  </nav>
</header>

<section class="hero">
  <div class="abs" style="inset:0" role="img" aria-label="Team of developers working on laptops in an open office"></div>
  <div class="hero-shade"></div>
  <h1>SOFTWARE<span>DEVELOPMENT CONSULTANCY</span></h1>
  <p>After spending more than twenty years each in the industry, including seven years in New York building electronic trading systems for Halden Brothers – the founders realised that there was a distinct lack in the market of people focusing</p>
  <div class="btn-outline">READ MORE</div>
  <div class="dots"><i class="on"></i><i></i><i></i></div>
</section>

<h2 class="sec-title" style="top:806px">WELCOME TO <em>BRIGHT KESTREL</em></h2>
<p class="sec-text" style="left:262px;top:860px;width:676px">After spending more than twenty years each in the industry, including seven years in New York building electronic trading systems for Halden Brothers – the founders realised that there was a distinct lack in the market of people focusing on how software is developed – not just solving the business problem, but automating the development itself to increase both productivity and software development experience. We combine a solid knowledge of computer quality.</p>
<div class="clients" role="img" aria-label="Client badges">
  <span></span><span></span><span></span><span></span><span></span>
</div>

<section class="services">
  <h2 class="sec-title" style="top:32px">OUR <em>SERVICES</em></h2>
  <p class="sec-text" style="left:0;top:82px;width:1200px">We are all about building software better, including seven years in New York building electronic</p>
  <div class="service" style="left:101px">
    <div class="icon" role="img" aria-label="Consulting icon"></div>
    <h3>CONSULTING</h3>
    <p>Up-skill your team by using our consultants - for<br>either short or long term engagements.</p>
  </div>
  <div class="service" style="left:451px">
    <div class="icon" role="img" aria-label="Projects icon"></div>
    <h3>PROJECTS</h3>
    <p>We can deliver a large project on a fixed price basis<br>at a quality standard you won't believe</p>
  </div>
  <div class="service" style="left:801px">
    <div class="icon" role="img" aria-label="Product icon"></div>
    <h3>TALLYWEB</h3>
    <p>Our product, TallyWeb, allows you to skip the devel-<br>opment cycle and turn an excel spreadsheet directly<br>into either a web service or a web site</p>
  </div>
</section>

<h2 class="sec-title" style="top:1645px">WHO <em>WE ARE</em></h2>
<p class="sec-text" style="left:0;top:1694px;width:1200px">We are all about building software better, including seven years in New York building electronic</p>
<div class="who-photo" role="img" aria-label="Developers at work in a bright open-plan office"></div>
<div class="who-card">
  <h3>SED UT PERSPICIATIS UNDE</h3>
  <p>Nemo enim ipsam voluptatem quia voluptas sit aspernatur aut odit aut fugit, sed quia consequuntur magni dolores eos qui ratione voluptatem sequi nesciunt.Neq ue porro quisquam est, qui dolorem ipsum quia dolor sit amet, consectetur adipi sci velit, sed quia non numquam eius modi tempora sed ut perspiciatis unde omnis iste natus error sit voluptatem accusantium doloremque laudantium, totam rem aperiam, eaque ipsa quae ab illo inventore veritatis et quasi architecto beatae vitae dicta sunt explicabo</p>
</div>

<section class="testimonial">
  <svg style="left:48px" width="20" height="90" viewBox="0 0 20 90" aria-hidden="true"><polyline points="18,2 2,45 18,88" fill="none" stroke="rgba(255,255,255,.5)" stroke-width="2"/></svg>
  <svg style="left:1132px" width="20" height="90" viewBox="0 0 20 90" aria-hidden="true"><polyline points="2,2 18,45 2,88" fill="none" stroke="rgba(255,255,255,.5)" stroke-width="2"/></svg>
  <span class="qmark" style="left:156px;top:62px">“</span>
  <p class="quote">Sed ut perspiciatis unde omnis iste natus error sit voluptatem accusantium doloremque laudantium, totam rem aperiam, eaque ipsa quae ab illo inventore veritatis et quasi architecto beatae vitae dicta sunt explicabo. Nemo enim ipsam voluptatem quia voluptas sit aspernatur aut odit aut fugit, sed quia consequuntur magni dolores eos qui ratione voluptatem sequi nesciunt</p>
  <span class="qmark" style="left:560px;top:176px">”</span>
  <h4>MARA QUILL</h4>
  <div class="date">Posted On 07 Sep 2018</div>
  <div class="avatar" role="img" aria-label="Portrait of the client giving the testimonial"></div>
</section>

<h2 class="sec-title" style="top:2636px">MEET OUR <em>LEADERSHIP TEAM</em></h2>
<p class="sec-text" style="left:250px;top:2685px;width:700px">Between just the partners, we have more than 60 years of software development experience. We combine a solid knowledge of computer science with a practical, pragmatic approach to delivering software.</p>

<div class="team-card" style="left:120px">
  <div class="portrait" role="img" aria-label="Portrait of partner Ravi Tollan"></div>
  <h4>RAVI TOLLAN</h4><div class="role">PARTNER</div>
  <p>Ravi's one of the best developers on the planet</p>
</div>
<div class="team-card" style="left:455px">
  <div class="portrait" role="img" aria-label="Portrait of partner Owen Plaskett"></div>
  <h4>OWEN PLASKETT</h4><div class="role">PARTNER</div>
  <p>Owen's been running software projects for 20 years</p>
</div>
<div class="team-card" style="left:790px">
  <div class="portrait" role="img" aria-label="Portrait of partner Tomas Veyne"></div>
  <h4>TOMAS VEYNE</h4><div class="role">PARTNER</div>
  <p>Tomas codes for fun as much as he does for work</p>
</div>

<footer class="site-footer">
  <div class="foot-brand"><div class="mark"></div><div class="name">BRIGHT KESTREL</div></div>
  <div class="foot-col" style="left:393px">
    <h4>CONTACT US</h4>
    <div class="item">ADDRESS<br>42 Harbour Lane, Sydney 2000</div>
    <div class="item">PHONE<br>(000)-555-0142</div>
    <div class="item">EMAIL<br>info@brightkestrel.com.au</div>
  </div>
  <div class="foot-col" style="left:636px">
    <h4>COMPANY</h4>
    <div class="link">HOME</div><div class="link">ABOUT US</div><div class="link">SERVICES</div><div class="link">BLOG</div><div class="link">TEAM</div><div class="link">CONTACT US</div>
  </div>
  <div class="foot-col" style="left:828px">
    <h4>KEEP IN TOUCH</h4>
    <div class="field">EMAIL ADDRESS</div>
    <div class="btn-red">SUBSCRIBE</div>
    <div class="socials" aria-label="Social links"><span></span><span></span><span></span><span></span><span></span></div>
  </div>
  <div class="foot-rule"></div>
  <div class="copyright">© Copyright 2018 Bright Kestrel.All rights reserved.</div>
</footer>

</body>
</html>
```